Vernac Law Business cards and stationary design project

We are looking for a stationary design for business cards (double sided), 8x10, 5x7, and legal and standard envelopes.

We would like the design to match the logo that we have already.
Color palate preferred is Teal, White, grey and any others that will look good for a professional law firm.

We would like this statement: "COUNSEL. CLARITY. COMMITMENT" to be on the back of the business cards and maybe on the stationary if it looks good.

Please see link to website for more information: www.vernac-law.example

Target Market(s)

Potential clients that need Attorney services.

Industry/Entity Type

Law Firm

Contact Information for Business Card

We would like the front and back to be two different colors. Current business cards are teal front, grey back and are a vertical design. We are open to options with colors.

Font styles to use
Serif

Colors
33a6d7
33b8a4
b9b9b9
5c5c5c

Requirements
Must have
• Logo supplied needs to go on the card and stationary.
• Match website color palate, www.vernac-law.example
• Be professional and not too wordy.
• Criminal Law, Civil Litigation, Personal Injury, Restraining Orders need to be on the card.
Nice to have
• RELATIONSHIPS. RESPECT. RESULTS. on the back of the card.
Should not have
• Not be too busy/wordy or too flashy.

```html
<!DOCTYPE html>
<html lang="en">
<head>
<meta charset="utf-8">
<title>Vernac Law – Business Card</title>
<link href="https://fonts.googleapis.com/css2?family=Open+Sans:wght@400;600;700&display=swap" rel="stylesheet">
<style>
  :root {
    --backdrop: #000000;
    --card: #333438;
    --card-edge: #3a3b40;
    --teal: #1c8b9b;
    --white: #ffffff;
    --rule: #4a4b50;
  }
  * { box-sizing: border-box; margin: 0; padding: 0; }
  html, body {
    width: 1200px; height: 900px; overflow: hidden;
    background: var(--backdrop);
    font-family: "Open Sans", Arial, sans-serif;
  }
  .stage { position: relative; width: 1200px; height: 900px; }
  .card {
    position: absolute; top: 271px; width: 457px; height: 281px;
    border-radius: 14px;
    background: linear-gradient(180deg, var(--card-edge), var(--card));
    overflow: hidden;
  }
  .card--front { left: 137px; }
  .card--back { left: 626px; }

  /* Front */
  .front-mark {
    position: absolute; left: 40px; top: 110px; width: 180px;
    text-align: center; color: var(--teal);
    font-size: 28px; font-weight: 600; line-height: 1.1;
  }
  .front-divider {
    position: absolute; left: 221px; top: 70px; width: 1px; height: 120px;
    background: var(--rule);
  }
  .contact { position: absolute; left: 256px; top: 35px; color: var(--white); }
  .contact__name { color: var(--teal); font-size: 16px; font-weight: 600; line-height: 1.2; }
  .contact__title { font-size: 12.5px; line-height: 1.3; }
  .contact__address { margin-top: 17px; font-size: 12.5px; line-height: 1.15; }
  .contact__list { list-style: none; margin-top: 17px; }
  .contact__list li {
    display: flex; align-items: center; gap: 8px;
    font-size: 12.5px; line-height: 19px;
  }
  .contact__list svg { width: 10px; height: 10px; fill: var(--teal); flex: none; }
  .practice {
    position: absolute; left: 0; right: 0; top: 234px;
    text-align: center; color: var(--teal);
    font-size: 12.2px; font-weight: 600; line-height: 1.3;
  }

  /* Back */
  .back-mark {
    position: absolute; left: 0; right: 0; top: 150px;
    text-align: center; color: var(--teal);
    font-size: 32px; font-weight: 400; letter-spacing: 1px;
  }
  .motto {
    position: absolute; left: 0; right: 0; top: 236px;
    display: flex; align-items: center; gap: 8px;
  }
  .motto__line { flex: 1; height: 2px; background: var(--white); }
  .motto__text { color: var(--white); font-size: 12.5px; font-weight: 600; white-space: nowrap; }
</style>
</head>
<body>
<main class="stage">
  <section class="card card--front">
    <div class="front-mark">Vernac Law</div>
    <div class="front-divider"></div>
    <div class="contact">
      <p class="contact__name">Daniel Marsh</p>
      <p class="contact__title">Managing Director</p>
      <p class="contact__address">12345, Address Goes Here<br>Country Name, 123456</p>
      <ul class="contact__list">
        <li><svg viewBox="0 0 10 10"><path d="M2 0.5l2 2-1 1.2c.6 1.3 1.6 2.3 2.9 2.9l1.2-1 2 2-1.2 1.6C4.8 9 1 5.2.5 1.7z"/></svg>(044)-456-7890</li>
        <li><svg viewBox="0 0 10 10"><rect x="1" y="3" width="8" height="6" rx="1"/><rect x="3" y="0.5" width="4" height="3"/></svg>123-456-7890</li>
        <li><svg viewBox="0 0 10 10"><path d="M0.5 2h9v6h-9z M0.8 2.3L5 5.5l4.2-3.2" /></svg>info@youremail.com</li>
        <li><svg viewBox="0 0 10 10"><circle cx="5" cy="5" r="4.5"/></svg>www.website.com</li>
      </ul>
    </div>
    <p class="practice">Practice areas, Criminal Law, Civil Litigation/Personal Injury<br>Restraining Orders</p>
  </section>

  <section class="card card--back">
    <div class="back-mark">Vernac Law</div>
    <div class="motto">
      <span class="motto__line"></span>
      <span class="motto__text">COUNSEL. CLARITY. COMMITMENT</span>
      <span class="motto__line"></span>
    </div>
  </section>
</main>
</body>
</html>
```